Sustainably Transforming Education

Company is education services based. early learning through adult and corporate. Focus is national government policy and program design and delivery alongside a research based and academically grounded set of approaches to planning, evaluation, and change management.I am looking for an innovative design position that aligns with the global agendas for innovation, creativity and collaboration at international and national policy levels (berulo is a name that reflects these qualities - colours need to reflect amythyst in some way). I also need a design that translates from a business card as 1 medium of interaction to a template that can work in word/powerpoint etc to support both stationery as well as a digital strategy across multiple channels (fb/twit/etc)There is no slogan/tag line for the company and their is no logo. I was looking to just leverage the name - have currently played around with various fonts (ending up with cuisine - all lowercase).

Industry/Entity Type

Adult

Contact Information for Business Card

name: berulo (all lowercase)Chairman: Andrew CrowMobile: +61 418 902 131Web: www.berulo.comemail: martin.pelly@berulo-example.com

Font styles to use
Script
Other font styles liked:
• cuisine

Colors
e34298
e667a6
33a6d7
aaaaaa

Requirements
Nice to have
• https://files.example-share.net/sh/qx7kw2hd91lzmnp/AAFr3tYbQeLp8VwZnKcDs2Hu?dl=0
• Link to the printwell templates used to begin this process....the one with the lines was about people intersecting (collaborating).....the organic shapes one more of a fluid feel of people coming together - the overall shape being largely spherical could represent a "global" feel.....anyway that is how I was thinking about these

```html
<!DOCTYPE html>
<html lang="en">
<head>
<meta charset="utf-8">
<title>berulo business card</title>
<link rel="stylesheet" href="https://fonts.googleapis.com/css2?family=Courgette&display=swap">
<style>
  :root {
    --page: #eeeeee;
    --band: #333333;
    --stripe-magenta: #e34298;
    --stripe-pink: #e667a6;
    --stripe-mist: #e4e1e8;
    --stripe-sky: #a6d8ee;
    --stripe-blue: #33a6d7;
    --name-blue: #33a6d7;
    --ink-light: #ffffff;
  }
  html, body {
    margin: 0;
    width: 1200px;
    height: 1152px;
    overflow: hidden;
    background: var(--page);
  }
  .canvas {
    position: relative;
    width: 1200px;
    height: 1152px;
  }
  .card {
    position: absolute;
    left: 160px;
    width: 880px;
    height: 503px;
    display: block;
    box-shadow: 0 3px 10px rgba(0,0,0,0.18);
  }
  .card--front { top: 52px; }
  .card--back { top: 597px; }
  .stripe--magenta { fill: var(--stripe-magenta); }
  .stripe--pink { fill: var(--stripe-pink); }
  .stripe--mist { fill: var(--stripe-mist); }
  .stripe--sky { fill: var(--stripe-sky); }
  .stripe--blue { fill: var(--stripe-blue); }
  .band { fill: var(--band); }
  .script { font-family: "Courgette", cursive; }
  .holder-name { fill: var(--name-blue); font-size: 64px; }
  .holder-role { fill: var(--ink-light); font-size: 30px; }
  .contact-line { fill: var(--ink-light); font-size: 23px; font-style: italic; }
  .brand-name { fill: var(--ink-light); font-size: 100px; }
</style>
</head>
<body>
<main class="canvas">
  <svg width="0" height="0" style="position:absolute" aria-hidden="true">
    <defs>
      <pattern id="stripes" patternUnits="userSpaceOnUse" width="880" height="220" patternTransform="rotate(-20)">
        <rect class="stripe--magenta" x="0" y="0" width="880" height="44"/>
        <rect class="stripe--pink" x="0" y="44" width="880" height="44"/>
        <rect class="stripe--mist" x="0" y="88" width="880" height="44"/>
        <rect class="stripe--sky" x="0" y="132" width="880" height="44"/>
        <rect class="stripe--blue" x="0" y="176" width="880" height="44"/>
      </pattern>
      <clipPath id="card-edge"><rect x="0" y="0" width="880" height="503"/></clipPath>
    </defs>
  </svg>

  <svg class="card card--front" viewBox="0 0 880 503" aria-label="Business card front">
    <g clip-path="url(#card-edge)">
      <rect class="card-field" x="0" y="0" width="880" height="503" fill="url(#stripes)"/>
      <g transform="rotate(-20 440 251)">
        <rect class="band band--top" x="330" y="30" width="800" height="70"/>
        <text class="script holder-name" x="60" y="190">Martin Pelly</text>
        <text class="script holder-role" x="80" y="226">Chairman</text>
        <rect class="band band--contact" x="-120" y="250" width="720" height="150"/>
        <text class="script contact-line" x="200" y="295">+61 427 315 086</text>
        <text class="script contact-line" x="200" y="334">martin.pelly@berulo-example.com</text>
        <text class="script contact-line" x="200" y="373">www.berulo-example.com</text>
      </g>
    </g>
  </svg>

  <svg class="card card--back" viewBox="0 0 880 503" aria-label="Business card back">
    <g clip-path="url(#card-edge)">
      <rect class="card-field" x="0" y="0" width="880" height="503" fill="url(#stripes)"/>
      <g transform="translate(235 250) rotate(70)">
        <rect class="band band--brand" x="-420" y="-58" width="840" height="116"/>
        <text class="script brand-name" x="0" y="32" text-anchor="middle">berulo</text>
      </g>
    </g>
  </svg>
</main>
</body>
</html>
```